Venture Capital Firm Needs Website Redesign

We need a bold revamp of our website (https://halverine.vc/)
which at the moment looks washed out. We want a crisp, fresh and unique look. Feel free to keep as much or as little content in the site. The only thing we need to keep is a team section. The site should convey a clear distinction between our 3 product lines: Venture Capital, Private Credit, and Crypto. Two versions of our logo are attached and they should not change. For design inspirations, we like http://www.9plm.com/ for a more simple site and for a more built out site we like http://bluetorch.com/

Updates
Industry/Entity Type
Investment
Coding
Coded - Design and coding required
Number of Pages Required
1 page
Font styles to use
Colors
Designer to choose colors to be used in the design.
Requirements
Must have
- - Clear distinction between our 3 product lines: Venture Capital, Private Credit
- - Team section

Nice to have
- Some really creative aspect like http://www.9plm.com/ has with the distinction between first, second, and third kind

```html
<!DOCTYPE html>
<html lang="en">
<head>
<meta charset="utf-8">
<title>Halverine</title>
<link href="https://fonts.googleapis.com/css2?family=Roboto+Condensed:wght@300;400&family=Arimo:wght@400&display=swap" rel="stylesheet">
<style>
:root{
  --green:#7f9a52;
  --green-soft:#8fa86b;
  --ink:#222;
  --grey-text:#333;
  --rule:#e4e4e4;
  --footer-bg:#f1f1f1;
  --white:#fff;
}
*{margin:0;padding:0;box-sizing:border-box}
html,body{width:762px;height:1200px;overflow:hidden;background:var(--white)}
body{position:relative;font-family:"Arimo",Arial,sans-serif;color:var(--ink)}
.head{font-family:"Roboto Condensed","Arial Narrow",sans-serif}
.abs{position:absolute}
/* header */
.site-header{position:absolute;left:0;top:0;width:762px;height:56px;background:var(--white)}
.brand{position:absolute;left:62px;top:12px;display:flex;align-items:center;gap:8px}
.brand-name{font-family:"Roboto Condensed",sans-serif;font-weight:300;font-size:26px;color:var(--green);letter-spacing:1px}
.main-nav a{position:absolute;top:29px;font-family:"Roboto Condensed",sans-serif;font-size:10.5px;color:var(--ink);text-decoration:none}
.main-nav a.current{color:var(--green);border-bottom:1px solid var(--green);padding-bottom:1px}
/* hero */
.hero{position:absolute;left:0;top:56px;width:762px;height:290px;
  background:linear-gradient(100deg,#dfe4ea 0%,#eef1f4 35%,#c9ced6 58%,#8d8f93 72%,#5b4a3c 85%,#3f3228 100%)}
.hero-title{position:absolute;left:63px;top:88px;font-family:"Roboto Condensed",sans-serif;font-size:21px;line-height:28px;color:#1d1d1d;width:320px}
.btn{position:absolute;display:flex;align-items:center;justify-content:center;border-radius:9px;font-family:"Roboto Condensed",sans-serif;font-size:10px;text-decoration:none}
.btn-green{background:var(--green);color:var(--white)}
.btn-white{background:var(--white);color:var(--green)}
.slide-arrow{position:absolute;top:193px;width:19px;height:18px;background:#3a3a3a;border:1px solid #fff;display:flex;align-items:center;justify-content:center}
/* services */
.service{position:absolute;top:376px;width:200px;text-align:center}
.service svg{display:block;margin:0 auto}
.service h3{font-family:"Roboto Condensed",sans-serif;font-weight:400;font-size:13px;margin-top:8px}
.service p{font-size:7.5px;line-height:12.5px;color:var(--grey-text);margin-top:7px}
.service a{display:inline-block;font-size:8.5px;color:var(--grey-text);margin-top:8px}
/* team */
.team{position:absolute;left:0;top:566px;width:762px;height:214px;text-align:center;color:var(--white)}
.team-photos{position:absolute;inset:0;background:linear-gradient(90deg,#93ab70,#8aa266 50%,#93ab70)}
.team h2{position:absolute;top:42px;width:100%;font-family:"Roboto Condensed",sans-serif;font-weight:400;font-size:21px}
.team .lead{position:absolute;top:74px;width:100%;font-family:"Roboto Condensed",sans-serif;font-size:14.5px;line-height:23px}
.team .values{position:absolute;top:124px;width:100%;font-family:"Roboto Condensed",sans-serif;font-size:15px;letter-spacing:.3px;word-spacing:10px}
/* about */
.about{position:absolute;left:0;top:780px;width:762px;height:208px;text-align:center}
.about h2{position:absolute;top:24px;width:100%;font-family:"Roboto Condensed",sans-serif;font-weight:400;font-size:21px;color:#222}
.about p{position:absolute;left:72px;top:62px;width:618px;font-size:9.4px;line-height:17.6px;color:var(--grey-text)}
/* footer */
.site-footer{position:absolute;left:0;top:988px;width:762px;height:188px;background:var(--footer-bg)}
.foot-col h4{font-family:"Roboto Condensed",sans-serif;font-weight:400;font-size:11.5px;color:#222}
.foot-col .rule{width:18px;height:1px;background:var(--green);margin-top:8px}
.quick-links{position:absolute;left:64px;top:18px}
.quick-links ul{list-style:none;margin-top:10px}
.quick-links li{font-family:"Roboto Condensed",sans-serif;font-size:9px;line-height:19.8px}
.newsletter{position:absolute;left:196px;top:18px;width:160px}
.newsletter p{font-size:7.5px;line-height:13px;margin-top:10px;color:#222}
.email-field{margin-top:10px;width:153px;height:24px;border:1px solid #ccc;background:var(--white);font-size:8px;color:#444;padding:7px 10px}
.subscribe{margin-top:15px;width:65px;height:24px;background:var(--green);color:#fff;font-family:"Roboto Condensed",sans-serif;font-size:10.5px;display:flex;align-items:center;justify-content:center}
.contact{position:absolute;left:392px;top:22px;width:140px}
.contact .org{font-family:"Roboto Condensed",sans-serif;font-size:11px;margin-top:12px;margin-left:4px}
.contact .addr{font-size:7.5px;line-height:12.5px;margin-top:6px;margin-left:3px}
.contact .row{display:flex;align-items:center;gap:9px;font-size:7.5px;margin-top:6px;margin-left:3px}
.socials{display:flex;gap:7px;margin-top:12px}
.socials span{width:18px;height:18px;border:1px solid #555;border-radius:50%}
.foot-brand{position:absolute;left:568px;top:30px;width:130px;text-align:center}
.foot-brand .brand-name{font-size:20px;display:block;margin-top:6px}
.copyright{position:absolute;left:0;top:1176px;width:762px;height:24px;background:var(--green);color:#fff;font-family:"Roboto Condensed",sans-serif;font-size:8px;display:flex;align-items:center;justify-content:center}
</style>
</head>
<body>

<header class="site-header">
  <div class="brand">
    <svg width="40" height="40" viewBox="0 0 40 40"><circle cx="20" cy="20" r="18" fill="none" stroke="#333" stroke-width="1.2"/></svg>
    <span class="brand-name">HALVERINE</span>
  </div>
  <nav class="main-nav">
    <a class="current" href="#" style="left:316px">Home</a>
    <a href="#" style="left:367px">Venture Capital</a>
    <a href="#" style="left:450px">Private Credit</a>
    <a href="#" style="left:525px">Crypto</a>
    <a href="#" style="left:571px">Team</a>
    <a href="#" style="left:613px">Blog</a>
    <a href="#" style="left:652px">Contact Us</a>
  </nav>
</header>

<section class="hero" role="img" aria-label="Photo of a climber helping another climber up a rock summit above snowy mountains and clouds">
</section>
<h1 class="hero-title" style="top:144px;font-weight:400">Halverine Operates At The Intersection of Technology And Novel Asset Classes.</h1>
<a class="btn btn-green" href="#" style="left:63px;top:238px;width:82px;height:18px">Learn More</a>
<div class="slide-arrow" style="left:4px"><svg width="8" height="8" viewBox="0 0 8 8"><path d="M5.5 1 2.5 4l3 3" stroke="#fff" stroke-width="1.5" fill="none"/></svg></div>
<div class="slide-arrow" style="left:734px"><svg width="8" height="8" viewBox="0 0 8 8"><path d="M2.5 1 5.5 4l-3 3" stroke="#fff" stroke-width="1.5" fill="none"/></svg></div>

<section class="services">
  <div class="service" style="left:69px">
    <svg width="80" height="76" viewBox="0 0 80 76">
      <circle cx="40" cy="38" r="36" fill="none" stroke="#bbb" stroke-width="1"/>
      <circle cx="4" cy="38" r="3" fill="#aaa"/><circle cx="76" cy="38" r="3" fill="#aaa"/>
      <circle cx="40" cy="30" r="10" fill="none" stroke="#7f9a52" stroke-width="1.5"/>
      <text x="40" y="34" font-size="11" text-anchor="middle" fill="#7f9a52" font-family="Arial">$</text>
      <path d="M22 46h10l8 4h12l6-3" fill="none" stroke="#7f9a52" stroke-width="1.5"/>
      <rect x="20" y="44" width="5" height="10" fill="none" stroke="#7f9a52" stroke-width="1.5"/>
    </svg>
    <h3>Venture Capital</h3>
    <p>We invest in early-stage startups led by founders who are passionate and knowledgeable...[+]</p>
    <a href="#">Read More</a>
  </div>
  <div class="service" style="left:281px;top:376px">
    <svg width="80" height="76" viewBox="0 0 80 76">
      <circle cx="40" cy="38" r="36" fill="none" stroke="#bbb" stroke-width="1"/>
      <circle cx="4" cy="38" r="3" fill="#aaa"/><circle cx="76" cy="38" r="3" fill="#aaa"/>
      <rect x="18" y="26" width="40" height="24" rx="2" fill="none" stroke="#7f9a52" stroke-width="1.5"/>
      <line x1="18" y1="32" x2="58" y2="32" stroke="#7f9a52" stroke-width="1.5"/>
      <circle cx="28" cy="42" r="3.5" fill="none" stroke="#7f9a52" stroke-width="1.5"/>
      <circle cx="50" cy="42" r="3.5" fill="none" stroke="#7f9a52" stroke-width="1.5"/>
    </svg>
    <h3 style="margin-top:13px">Private Credit</h3>
    <p>Halverine Private Credit provides capital to lending businesses that are focused on using technology..[+]</p>
    <a href="#">Read More</a>
  </div>
  <div class="service" style="left:493px">
    <svg width="80" height="76" viewBox="0 0 80 76">
      <circle cx="40" cy="38" r="36" fill="none" stroke="#bbb" stroke-width="1"/>
      <circle cx="4" cy="38" r="3" fill="#aaa"/><circle cx="76" cy="38" r="3" fill="#aaa"/>
      <rect x="22" y="44" width="4" height="10" fill="#7f9a52"/>
      <rect x="30" y="38" width="4" height="16" fill="#7f9a52"/>
      <rect x="38" y="32" width="4" height="22" fill="#7f9a52"/>
      <path d="M22 38 40 24l8 4 10-10" fill="none" stroke="#7f9a52" stroke-width="1.5"/>
      <path d="M52 18h6v6" fill="none" stroke="#7f9a52" stroke-width="1.5"/>
    </svg>
    <h3 style="margin-top:13px">Crypto</h3>
    <p>The Halverine Crypto Index tracks the top 15 crypto currencies weighted by market cap &amp; rebalanced...[+]</p>
    <a href="#">Read More</a>
  </div>
</section>

<section class="team">
  <div class="team-photos" role="img" aria-label="Grid of team member portrait photos under a green tint"></div>
  <h2>Our Team</h2>
  <p class="lead">Our Highly Skilled Financial Consultants Are People Who Personifies The Very Qualities<br>That Have Made Us Successful</p>
  <p class="values">KNOWLEDGE. EXPERIENCE. ENTHUSIAM. DEDICATION</p>
  <a class="btn btn-white" href="#" style="left:340px;top:156px;width:82px;height:17px">Read More</a>
</section>

<section class="about">
  <h2>About Us</h2>
  <p>Halverine operates three businesses that bridge technology and finance. We invest in pre-seed venture capital, and build software for the companies we invest in. We manage direct private credit funds that provide private credit capital to alternative private credit platforms, enabling them to finance the loans they originate. We create crypto funds for individuals, IRAs and institutions to get simple and easy access to cryptocurrencies.</p>
  <a class="btn btn-green" href="#" style="left:340px;top:146px;width:82px;height:17px">Call Us Today</a>
</section>

<footer class="site-footer">
  <div class="foot-col quick-links">
    <h4>Quick Links</h4><div class="rule"></div>
    <ul><li>Home</li><li>Venture Capital</li><li>Private Credit</li><li>Crypto</li><li>Team</li><li>Blog</li></ul>
  </div>
  <div class="foot-col newsletter">
    <h4>Newsletter Signup</h4><div class="rule"></div>
    <p>Lorem ipsum dolor sit amet, sectetuer adipiscing elit, sed diam nonummy nibh euismod tincidunt.</p>
    <div class="email-field">Enter Your Email&nbsp; Here</div>
    <div class="subscribe">Subscribe</div>
  </div>
  <div class="foot-col contact">
    <h4>Contact Details</h4><div class="rule"></div>
    <div class="org">Halverine</div>
    <div class="addr">218 Larkmoor Avenue, Suite 406<br>Eastbrook, NY 10871</div>
    <div class="row"><svg width="9" height="9" viewBox="0 0 10 10"><path d="M2 1l2 2-1 1.5c.8 1.5 1.5 2.2 3 3L7.5 6l2 2-1.5 1.5C4.5 9 1 5.5.5 1.5z" fill="#7f9a52"/></svg>555-018-4721</div>
    <div class="row"><svg width="10" height="8" viewBox="0 0 10 8"><rect x=".5" y=".5" width="9" height="7" fill="none" stroke="#7f9a52"/><path d="M.5.5 5 4.5 9.5.5" fill="none" stroke="#7f9a52"/></svg>info@halverine.vc</div>
    <div class="socials"><span></span><span></span><span></span><span></span></div>
  </div>
  <div class="foot-brand">
    <svg width="84" height="84" viewBox="0 0 84 84"><circle cx="42" cy="42" r="40" fill="none" stroke="#333" stroke-width="1.4"/></svg>
    <span class="brand-name">HALVERINE</span>
  </div>
</footer>
<div class="copyright">Copyright © 2018 Halverine . All Rights Reserved</div>

</body>
</html>
```